Professional BIO Template with photo and logo

Hello,
I need a professional Bio template developed via Microsoft WORD ASAP!!!!! I would like to just be able to add the text I need to add. So resize-able text boxes. Potentially able to adjust the font. These are the things I need added it to include.
Head shot (attached)
Text Box for Name
Text Box for phone number
Text box for email
KVT Logo (attached)
Maybe a blue banner at the top or some background boxes that are blue or grey. Here are the pantone colors that our company uses.

CORE COLOR
100c 91m 17y 6k 38r 58g 128b Hex #263A80 Pantone 7687 C

CORE CONTRAST COLOR
36c 29m 28y 0k 168r 168g 170b Hex #669999 Pantone Cool Gray 6C

I also attached some examples of what we have been looking at. Instead of green add the blue...instead of black maybe just be white.

Thank you

```html
<!DOCTYPE html>
<html lang="en">
<head>
<meta charset="utf-8">
<title>Daniel Hartwell — Bio</title>
<link rel="stylesheet" href="https://fonts.googleapis.com/css2?family=IBM+Plex+Sans:wght@400;500;600;700&family=Playfair+Display:wght@700;900&display=swap">
<style>
  :root {
    --core-blue: #263A80;
    --contrast-teal: #669999;
    --paper: #FFFFFF;
    --ink: #1A1A1A;
    --photo-dark: #3A3A3A;
    --photo-light: #8C8C8C;
  }
  * { margin: 0; padding: 0; box-sizing: border-box; }
  html, body { width: 927px; height: 1200px; overflow: hidden; background: var(--paper); }
  .bio-sheet {
    position: relative;
    width: 927px;
    height: 1200px;
    overflow: hidden;
    background: var(--paper);
    font-family: "IBM Plex Sans", Arial, sans-serif;
    color: var(--ink);
  }
  .header-band {
    position: absolute;
    left: 0; top: 0;
    width: 927px; height: 220px;
    background: var(--core-blue);
  }
  .headshot {
    position: absolute;
    left: 71px; top: 54px;
    width: 228px; height: 296px;
    border-radius: 114px 114px 0 0;
    background: radial-gradient(ellipse at 50% 35%, var(--photo-light) 0%, #666 45%, var(--photo-dark) 100%);
  }
  .person-name {
    position: absolute;
    left: 363px; top: 78px;
    font-family: "Playfair Display", Georgia, serif;
    font-weight: 900;
    font-size: 52px;
    line-height: 1;
    letter-spacing: -0.5px;
    color: var(--paper);
  }
  .person-role {
    position: absolute;
    left: 363px; top: 143px;
    font-size: 30px;
    font-weight: 400;
    line-height: 1;
    color: var(--paper);
  }
  .contact-row {
    position: absolute;
    left: 370px;
    display: flex;
    align-items: center;
    gap: 20px;
    color: var(--core-blue);
    font-weight: 600;
    font-size: 26px;
    line-height: 1;
  }
  .contact-row svg { width: 27px; height: 27px; flex: none; }
  .contact-phone { top: 251px; }
  .contact-email { top: 317px; }
  .contact-divider {
    position: absolute;
    left: 366px; top: 297px;
    width: 332px; height: 2px;
    background: var(--core-blue);
  }
  .company-mark {
    position: absolute;
    left: 726px; top: 250px;
    width: 135px; height: 107px;
    display: flex;
    align-items: center;
    justify-content: center;
    font-size: 38px;
    font-weight: 700;
    letter-spacing: 2px;
    color: var(--core-blue);
  }
  .about-title {
    position: absolute;
    left: 67px; top: 416px;
    font-family: "Playfair Display", Georgia, serif;
    font-weight: 900;
    font-size: 33px;
    line-height: 1;
    color: var(--core-blue);
  }
  .about-body {
    position: absolute;
    left: 67px; top: 488px;
    width: 794px;
    font-size: 20.3px;
    line-height: 29px;
    text-align: justify;
  }
  .about-body p + p { margin-top: 40px; }
  .about-body p:last-child { text-align: left; }
  .footer-band {
    position: absolute;
    left: 0; top: 1143px;
    width: 927px; height: 57px;
    background: var(--contrast-teal);
    color: var(--paper);
  }
  .footer-note {
    position: absolute;
    left: 0; width: 927px; top: 17px;
    text-align: center;
    font-size: 17.5px;
    line-height: 1;
  }
  .page-code {
    position: absolute;
    right: 21px; top: 15px;
    font-size: 20px;
    line-height: 1;
  }
</style>
</head>
<body>
<main class="bio-sheet">
  <div class="header-band"></div>
  <div class="headshot" role="img" aria-label="Headshot photograph of Daniel Hartwell"></div>

  <h1 class="person-name">Daniel Hartwell</h1>
  <p class="person-role">Developer</p>

  <div class="contact-row contact-phone">
    <svg viewBox="0 0 24 24" aria-hidden="true">
      <path fill="currentColor" d="M6.6 2.5c.5-.3 1.1-.2 1.4.3l2 3.2c.3.5.2 1.1-.2 1.4L8.3 8.6c.9 2.5 2.7 4.5 5.1 5.8l1.3-1.4c.4-.4 1-.5 1.5-.2l3.2 1.9c.5.3.7.9.4 1.4l-1.2 2.5c-.4.8-1.3 1.2-2.2 1C9.6 18.3 4.8 13.3 3.7 6.5c-.1-.9.3-1.7 1.1-2.1z"/>
      <path fill="none" stroke="currentColor" stroke-width="1.8" stroke-linecap="round" d="M14 6.5a4 4 0 0 1 3.5 3.5M14.3 2.8a7.5 7.5 0 0 1 6.9 6.9"/>
    </svg>
    <span>(555) 555 0142</span>
  </div>
  <div class="contact-divider"></div>
  <div class="contact-row contact-email">
    <svg viewBox="0 0 24 24" aria-hidden="true">
      <rect x="2" y="5" width="20" height="14" fill="none" stroke="currentColor" stroke-width="1.6"/>
      <path d="M2 5l10 8 10-8M2 19l7.5-7.5M22 19l-7.5-7.5" fill="none" stroke="currentColor" stroke-width="1.6"/>
    </svg>
    <span>danielhartwell@kvtmail.com</span>
  </div>

  <div class="company-mark">KVT</div>

  <h2 class="about-title">ABOUT</h2>
  <section class="about-body">
    <p>There are many variations of passages of Lorem Ipsum available, but the majority have suffered alteration in some form, by injected humour, or randomised words which don't look even slightly believable. If you are going to use a passage of Lorem Ipsum, you need to be sure there isn't anything embarrassing hidden in the middle of text. All the Lorem Ipsum generators on the Internet tend to repeat predefined chunks as necessary</p>
    <p>Sed ut perspiciatis unde omnis iste natus error sit voluptatem accusantium doloremque laudantium, totam rem aperiam, eaque ipsa quae ab illo inventore veritatis et quasi architecto beatae vitae dicta sunt explicabo. Nemo enim ipsam voluptatem quia voluptas sit aspernatur aut odit aut fugit, sed quia consequuntur magni dolores eos qui ratione voluptatem sequi nesciunt. Neque porro quisquam est, qui dolorem ipsum quia dolor sit amet, consectetur, adipisci velit,</p>
    <p>But I must explain to you how all this mistaken idea of denouncing pleasure and praising pain was born and I will give you a complete account of the system, and expound the actual teachings of the great explorer of the truth, the master-builder of human happiness. No one rejects, dislikes, or avoids pleasure itself, because it is pleasure, but because those who do not know how to pursue pleasure rationally encounter consequences that are extremely painful.</p>
  </section>

  <footer class="footer-band">
    <p class="footer-note">There are many variations of passages of Lorem Ipsum</p>
    <span class="page-code">X37</span>
  </footer>
</main>
</body>
</html>
```